Heron Loan Partners Business Card

We need a business card design for our mortgage servicing company. In addition to servicing the loans of homeowners, we help homeowners with purchasing their homes and any mortgage refinancing. We would like to see designs that use the colors in the logo attached below (gold-ish yellow and navy blue), and any other design you deem fit! The design should communicate a simpler life with smart mortgages provided by Heron.

```html
<!DOCTYPE html>
<html lang="en">
<head>
<meta charset="utf-8">
<title>Heron Loan Partners Business Card</title>
<link href="https://fonts.googleapis.com/css2?family=Arimo:wght@400;700&display=swap" rel="stylesheet">
<style>
  :root {
    --navy: #2b2a5c;
    --gold: #c9a132;
    --paper: #f7f7f8;
    --ink: #2f2f3a;
    --backdrop: #e4e4e8;
  }
  * { box-sizing: border-box; margin: 0; padding: 0; }
  html, body { width: 1200px; height: 912px; overflow: hidden; }
  body {
    background: var(--backdrop);
    font-family: "Arimo", Arial, sans-serif;
    position: relative;
  }
  .card {
    position: absolute;
    width: 560px;
    height: 320px;
    background: var(--paper);
    box-shadow: 0 6px 18px rgba(0,0,0,0.18);
  }
  .card--front { left: 40px; top: 120px; }
  .card--back { left: 600px; top: 480px; }

  .brand {
    display: flex;
    align-items: center;
    gap: 12px;
    color: var(--gold);
    font-weight: 700;
    white-space: nowrap;
  }
  .brand__dot {
    border-radius: 50%;
    background: var(--navy);
    flex: none;
  }
  .card--front .brand {
    position: absolute;
    left: 50%;
    top: 118px;
    transform: translateX(-50%);
    font-size: 44px;
  }
  .card--front .brand__dot { width: 22px; height: 22px; }
  .front__url {
    position: absolute;
    left: 300px;
    top: 212px;
    font-size: 15px;
    letter-spacing: 2.5px;
    color: var(--ink);
  }

  .card--back .brand {
    position: absolute;
    right: 40px;
    top: 40px;
    font-size: 26px;
    gap: 8px;
  }
  .card--back .brand__dot { width: 14px; height: 14px; }
  .back__rule {
    position: absolute;
    left: 30px;
    right: 30px;
    top: 150px;
    height: 1px;
    background: var(--navy);
  }
  .contact {
    position: absolute;
    right: 30px;
    top: 164px;
    list-style: none;
    text-align: right;
    font-size: 15px;
    line-height: 21px;
    color: var(--ink);
  }
  .contact li { display: flex; justify-content: flex-end; align-items: center; gap: 8px; }
  .contact svg { width: 12px; height: 12px; fill: var(--gold); flex: none; }
  .person {
    position: absolute;
    left: 30px;
    bottom: 30px;
  }
  .person__name { font-size: 24px; font-weight: 700; color: var(--gold); line-height: 28px; }
  .person__title { font-size: 16px; color: var(--navy); line-height: 20px; }
  .person__rule { width: 180px; height: 1px; background: var(--navy); margin: 10px 0 12px; }
  .person__address { font-size: 16px; line-height: 21px; color: var(--ink); font-style: normal; }
</style>
</head>
<body>
  <section class="card card--front" aria-label="Card front">
    <div class="brand"><span class="brand__dot"></span>Heron Mortgage</div>
    <p class="front__url">www.heron.com</p>
  </section>

  <section class="card card--back" aria-label="Card back">
    <div class="brand"><span class="brand__dot"></span>Heron Mortgage</div>
    <div class="back__rule"></div>
    <ul class="contact">
      <li>(555) 0142-7781
        <svg viewBox="0 0 12 12"><path d="M2.5 1l2 2.3-1 1.2a7 7 0 0 0 4 4l1.2-1 2.3 2-1.3 1.5C5.5 11 1 6.5 1 2.3z"/></svg>
      </li>
      <li>name@heron.com
        <svg viewBox="0 0 12 12"><path d="M0 2.5h12v7H0z M0 2.5l6 4 6-4" fill="var(--gold)" stroke="var(--paper)" stroke-width="0.9"/></svg>
      </li>
      <li>www.heron.com
        <svg viewBox="0 0 12 12"><circle cx="6" cy="6" r="5.5"/></svg>
      </li>
    </ul>
    <div class="person">
      <p class="person__name">Laura Bennett</p>
      <p class="person__title">President</p>
      <div class="person__rule"></div>
      <address class="person__address">2710 Alder Crest Lane<br>Brookhaven, NY 11719</address>
    </div>
  </section>
</body>
</html>
```